Morlavik APP redesign and color change

I am looking for a new design for my app. Please see the attached current design.

Currently, I have a functioning app but the colors and design are awful!
The logo is great but the rest of the app needs a refresh.
(Logo hi res not yet available but will upload soon.)
New colors or anything that is cutting edge.

Basically: It is a secure social media app within a school system where the teachers, students and parents can text, exchange photos, plan curriculum, etc.

I NEED ONLY landing page with a new look!
Looking for one distinct design for the landing page with new look.
The developer will apply this one design towards the rest of the pages/app screens.

Because part of the social media I need the feel and look of what is now the trend. Something that will attract and keep the client(s) interested. I am really leaving all the creative work to the designer and open to any suggestions.

Target Market(s)

Schools, community, teachers, students, colleges, sport teams

Industry/Entity Type

Non Profit

Font styles to use
Serif
Sans Serif

Colors

Designer to choose colors to be used in the design.

Requirements
Must have
• Sharp, trendy, millennial feel
Nice to have
• Up to designer
Should not have
• Up to designer

```html
<!DOCTYPE html>
<html lang="en">
<head>
<meta charset="utf-8">
<title>Morlavik — Sign In</title>
<link href="https://fonts.googleapis.com/css2?family=Lato:wght@400;700;900&family=Roboto:wght@400&display=swap" rel="stylesheet">
<style>
  :root {
    --olive-dark: #3a4a00;
    --olive-deep: #2f3d05;
    --olive-band: #4d6402;
    --gold: #b87a00;
    --gold-label: #b8862a;
    --card-glass: rgba(255, 252, 238, 0.82);
    --ink: #2a2a2a;
    --rule: #6b6b6b;
    --white: #ffffff;
    --meadow-light: #eef3cf;
    --meadow-mid: #b9cf5a;
    --meadow-deep: #6f8f22;
  }
  * { box-sizing: border-box; margin: 0; padding: 0; }
  html, body {
    width: 741px;
    height: 1200px;
    overflow: hidden;
    background: var(--olive-deep);
  }
  .screen {
    position: relative;
    width: 741px;
    height: 1200px;
    overflow: hidden;
    font-family: "Lato", sans-serif;
  }
  .hero-photo {
    position: absolute;
    left: 0; top: 0;
    width: 741px;
    height: 1024px;
    background:
      radial-gradient(ellipse 420px 520px at 560px 520px, rgba(250, 236, 214, 0.75), transparent 70%),
      linear-gradient(180deg, var(--meadow-light) 0%, #d9e6a0 25%, var(--meadow-mid) 55%, var(--meadow-deep) 100%);
  }
  .footer-band {
    position: absolute;
    left: 0; top: 1024px;
    width: 741px;
    height: 176px;
    background: linear-gradient(180deg, var(--olive-deep) 0%, var(--olive-band) 100%);
  }
  .brand {
    position: absolute;
    left: 0; top: 375px;
    width: 741px;
    text-align: center;
  }
  .brand-mark {
    display: block;
    margin: 0 auto 36px;
  }
  .brand-name {
    font-family: "Lato", sans-serif;
    font-weight: 900;
    font-size: 36px;
    letter-spacing: 22px;
    padding-left: 22px;
    color: var(--olive-dark);
  }
  .login-card {
    position: absolute;
    left: 93px; top: 653px;
    width: 556px;
    height: 317px;
    background: var(--card-glass);
    padding: 58px 62px 0;
  }
  .field-label {
    display: block;
    font-size: 16px;
    font-weight: 400;
    letter-spacing: 1.5px;
    color: var(--gold-label);
    text-transform: uppercase;
  }
  .field-value {
    font-family: "Roboto", sans-serif;
    font-size: 23px;
    color: var(--ink);
    margin-top: 20px;
    padding-bottom: 26px;
    border-bottom: 1.5px solid var(--rule);
  }
  .field + .field { margin-top: 30px; }
  .password-dots {
    display: flex;
    gap: 8px;
    margin-top: 32px;
  }
  .password-dots span {
    width: 9px; height: 9px;
    border-radius: 50%;
    background: var(--ink);
  }
  .submit-button {
    position: absolute;
    left: 93px; top: 970px;
    width: 556px;
    height: 106px;
    background: var(--gold);
    display: flex;
    align-items: center;
    justify-content: space-between;
    padding: 0 60px 0 62px;
    color: var(--white);
    font-size: 22px;
    font-weight: 400;
    box-shadow: 0 10px 24px rgba(0, 0, 0, 0.18);
  }
  .register-link {
    position: absolute;
    left: 0; top: 1119px;
    width: 741px;
    text-align: center;
    color: #f2f0dc;
    font-size: 18px;
  }
</style>
</head>
<body>
  <main class="screen">
    <div class="hero-photo" role="img" aria-label="Smiling woman reading a book while sitting on the grass under a tree in a sunny park"></div>
    <div class="footer-band"></div>

    <div class="brand">
      <svg class="brand-mark" width="70" height="70" viewBox="0 0 70 70" aria-hidden="true">
        <circle cx="35" cy="35" r="33" fill="var(--gold)"/>
      </svg>
      <div class="brand-name">MORLAVIK</div>
    </div>

    <form class="login-card">
      <div class="field">
        <label class="field-label">Username</label>
        <div class="field-value">lena@morlavik.org</div>
      </div>
      <div class="field">
        <label class="field-label">Password</label>
        <div class="password-dots">
          <span></span><span></span><span></span><span></span><span></span><span></span><span></span><span></span>
        </div>
      </div>
    </form>

    <div class="submit-button">
      <span>Get Started</span>
      <svg width="14" height="18" viewBox="0 0 14 18" aria-hidden="true">
        <polygon points="0,0 14,9 0,18" fill="#111"/>
      </svg>
    </div>

    <p class="register-link">Not registered? Create Account</p>
  </main>
</body>
</html>
```